Exciting & Elegant Stationary Pack

Stationary consists of
1. Letter head / Envelope
2. Business Card
3. Invoice
4. 40x40mm sticker

Attached files;

1. Logo (Other formats available on request)
2. MS word Doc - For information and description of design
3. Website image (This will be our new website so use the colours so everything ties together)
4. Sample of stationary pack we like, but feel free to be creative

Target Market(s)

Home improvement

Industry/Entity Type

Construction

Font styles to use
Other font styles liked:
• Leave up to designer - We like font used on (website attached image)

Requirements
Must have
• Please look at uploaded file of sample website and use colours
Nice to have
• Any type of business card design - eg. metal, die cut, embossed, etc...

```html
<!DOCTYPE html>
<html lang="en">
<head>
<meta charset="utf-8">
<title>Tessera Works – Business Card</title>
<link rel="stylesheet" href="https://fonts.googleapis.com/css2?family=PT+Sans:wght@400;700&display=swap">
<style>
  :root {
    --navy: #0b426b;
    --orange: #f28a30;
    --white: #ffffff;
    --marble-light: #f1f1ee;
    --marble-mid: #dcdcd8;
    --stage: #6b6b6b;
    --shadow: rgba(0, 0, 0, 0.35);
  }
  * { box-sizing: border-box; margin: 0; padding: 0; }
  html, body {
    width: 1200px;
    height: 750px;
    overflow: hidden;
  }
  body {
    background: var(--stage);
    font-family: "PT Sans", Arial, sans-serif;
    position: relative;
  }
  .card {
    position: absolute;
    width: 462px;
    height: 263px;
    background: var(--navy);
    box-shadow: 0 6px 10px var(--shadow);
    overflow: hidden;
  }
  .card--front { left: 308px; top: 105px; }
  .card--back  { left: 475px; top: 413px; }

  .card__art {
    position: absolute;
    inset: 0;
    width: 100%;
    height: 100%;
  }

  .contact {
    position: absolute;
    right: 23px;
    top: 10px;
    text-align: right;
    color: var(--white);
    font-size: 13.5px;
    line-height: 1.3;
  }
  .contact__name {
    color: var(--orange);
    font-weight: 700;
    font-size: 19px;
    line-height: 1.2;
  }
  .contact__role { margin-bottom: 8px; }
  .contact__licence { margin-bottom: 8px; }
  .contact__label {
    color: var(--orange);
    font-weight: 700;
  }

  .brand {
    position: absolute;
    font-weight: 700;
    display: flex;
    align-items: center;
    gap: 8px;
    white-space: nowrap;
  }
  .brand__square {
    width: 14px;
    height: 14px;
    background: currentColor;
  }
  .brand--front {
    left: 34px;
    top: 132px;
    color: var(--navy);
    font-size: 24px;
  }
  .brand--back {
    left: 50%;
    top: 50%;
    transform: translate(-50%, -50%);
    color: var(--white);
    font-size: 28px;
  }
</style>
</head>
<body>

  <section class="card card--front" aria-label="Business card front">
    <svg class="card__art" viewBox="0 0 462 263" preserveAspectRatio="none">
      <defs>
        <linearGradient id="marbleTone" x1="0" y1="0" x2="1" y2="1">
          <stop offset="0" stop-color="var(--marble-mid)"/>
          <stop offset="0.5" stop-color="var(--marble-light)"/>
          <stop offset="1" stop-color="var(--marble-mid)"/>
        </linearGradient>
      </defs>
      <polygon class="card__marble" role="img" aria-label="White marble stone texture"
               points="0,0 84,0 372,263 0,263" fill="url(#marbleTone)"/>
      <polygon class="card__stripe" points="150,70 396,263 376,263" fill="var(--orange)"/>
    </svg>

    <div class="brand brand--front">
      <span class="brand__square"></span>
      <span class="brand__name">Tessera Works</span>
    </div>

    <div class="contact">
      <p class="contact__name">Lena Marsh</p>
      <p class="contact__role">Project Manager</p>
      <p class="contact__licence">Lic No.,204619c</p>
      <p class="contact__phone"><span class="contact__label">C :</span> 0400 555 123</p>
      <p class="contact__email">info@tesseraworks.com.au</p>
      <p class="contact__web">www.tesseraworks.com.au</p>
    </div>
  </section>

  <section class="card card--back" aria-label="Business card back">
    <div class="brand brand--back">
      <span class="brand__square"></span>
      <span class="brand__name">Tessera Works</span>
    </div>
  </section>

</body>
</html>
```